New Business Card for Web Design/Internet Marketing Company

Looking for a great looking new business card. We are a 10 year old web design, internet marketing and website management company that works mostly with small businesses.

Our new card needs to better match the colors and style of our website, be bold, extremely usable and slightly edgy.

Target Market(s)

Small/Medium businesses that have websites

Industry/Entity Type

Internet

Requirements
Must have
• Front and back design, full color, rounded corners please

Must use the colors/style of our website (JPG provided)

INFO FOR CARDS (as readable as possible please)
Mark Lenner
President/CEO
mark@trelvanmedia.example
Phone: 520-381-7459
Toll Free: 866-381-7459
Address: 4315 W. Calloway Ave. Ste. 140, Tucson, AZ 85792

THINGS I WANT TO PROMOTE (if there is room):
1. Our Website - www.trelvanmedia.example

2. Social Media
Twitter: @trelvanmedia
Facebook: www.facebook.com/trelvanmedia

3. Our Services
Web Design
Internet Marketing
Website Management

```html
<!DOCTYPE html>
<html lang="en">
<head>
<meta charset="utf-8">
<title>Trelvan Media Business Card</title>
<link rel="stylesheet" href="https://fonts.googleapis.com/css2?family=PT+Sans:wght@400;700&display=swap">
<style>
  :root {
    --backdrop: #ece7df;
    --navy: #0b1730;
    --blue: #1f97d2;
    --blue-light: #2fa6dd;
    --orange: #f28a2e;
    --white: #ffffff;
    --divider: #5d6679;
  }
  * { box-sizing: border-box; margin: 0; padding: 0; }
  html, body { width: 1200px; height: 413px; overflow: hidden; }
  body {
    background: var(--backdrop);
    font-family: "PT Sans", Arial, sans-serif;
    position: relative;
  }
  .card {
    position: absolute;
    top: 60px;
    width: 512px;
    height: 291px;
    border-radius: 16px;
    overflow: hidden;
  }
  .card--front { left: 58px; background: var(--navy); }
  .card--back { left: 622px; background: var(--blue); color: var(--white); }

  .brand {
    position: absolute;
    left: 30px;
    top: 108px;
    width: 230px;
    display: flex;
    align-items: center;
    gap: 10px;
    font-size: 30px;
    font-weight: 700;
    color: var(--orange);
    line-height: 1;
  }
  .brand__dot {
    width: 18px; height: 18px;
    border-radius: 50%;
    background: var(--blue);
    flex: none;
  }
  .divider {
    position: absolute;
    left: 275px; top: 62px;
    width: 1px; height: 136px;
    background: var(--divider);
  }
  .contact {
    position: absolute;
    left: 290px; top: 74px;
    list-style: none;
    color: var(--white);
    font-size: 13px;
    line-height: 18.5px;
  }
  .contact li { display: flex; align-items: center; gap: 7px; }
  .contact svg { width: 10px; height: 10px; flex: none; }
  .address {
    position: absolute;
    left: 290px; top: 163px;
    color: var(--white);
    font-size: 13px;
    line-height: 17px;
    font-style: normal;
  }
  .wave { position: absolute; left: 0; top: 0; width: 512px; height: 291px; }
  .person {
    position: absolute;
    left: 32px; top: 268px;
    color: var(--white);
    font-size: 17px;
    font-weight: 700;
  }
  .person__title { font-size: 13px; font-weight: 400; }

  .ghost-name {
    position: absolute;
    left: 0; right: 0; top: 95px;
    text-align: center;
    font-size: 84px;
    font-weight: 700;
    color: var(--blue-light);
    line-height: 1;
  }
  .services {
    position: absolute;
    left: 0; right: 0; top: 124px;
    list-style: none;
    text-align: center;
    font-size: 20px;
    font-weight: 700;
    line-height: 27px;
  }
  .services li { display: inline-block; margin: 0 8px; }
  .services li::before {
    content: "";
    display: inline-block;
    width: 9px; height: 9px;
    border-radius: 50%;
    background: var(--white);
    margin-right: 7px;
    vertical-align: 3px;
  }
  .social {
    position: absolute;
    left: 0; right: 0; top: 242px;
    display: flex;
    justify-content: center;
    gap: 16px;
    font-size: 17px;
  }
  .social span { display: flex; align-items: center; gap: 6px; }
  .social i {
    width: 13px; height: 13px;
    background: var(--white);
    border-radius: 2px;
    display: inline-block;
  }
</style>
</head>
<body>
  <section class="card card--front" aria-label="Business card front">
    <div class="brand"><span class="brand__dot"></span>Trelvan Media</div>
    <div class="divider"></div>
    <ul class="contact">
      <li><svg viewBox="0 0 10 10"><circle cx="5" cy="5" r="5" fill="#f28a2e"/><path d="M3 3l1.2-.4.8 1.4-.8.6a3 3 0 0 0 1.4 1.4l.6-.8 1.4.8L7 7.2C5 7.2 2.8 5 3 3z" fill="#0b1730"/></svg>866-381-7459</li>
      <li><svg viewBox="0 0 10 10"><circle cx="5" cy="5" r="5" fill="#f28a2e"/><path d="M3 3l1.2-.4.8 1.4-.8.6a3 3 0 0 0 1.4 1.4l.6-.8 1.4.8L7 7.2C5 7.2 2.8 5 3 3z" fill="#0b1730"/></svg>520-381-7459</li>
      <li><svg viewBox="0 0 10 10"><circle cx="5" cy="5" r="5" fill="#f28a2e"/><rect x="2.5" y="3.3" width="5" height="3.6" fill="#0b1730"/><path d="M2.5 3.3L5 5.3l2.5-2" stroke="#f28a2e" stroke-width=".6" fill="none"/></svg>mark@trelvanmedia.example</li>
      <li><svg viewBox="0 0 10 10"><circle cx="5" cy="5" r="5" fill="#f28a2e"/><path d="M1 5h8M5 1v8" stroke="#0b1730" stroke-width=".7"/></svg>www.trelvanmedia.example</li>
    </ul>
    <address class="address">4315 W. Calloway Ave. Ste. 140<br>Tucson, AZ 85792</address>
    <svg class="wave" viewBox="0 0 512 291" aria-hidden="true">
      <path d="M0 244 C140 228 250 268 360 254 C430 245 480 232 512 222 L512 232 C470 246 420 258 360 266 C250 280 140 246 0 258 Z" fill="#f28a2e"/>
      <path d="M0 258 C140 246 250 280 360 266 C420 258 470 246 512 232 L512 291 L0 291 Z" fill="#1f97d2"/>
    </svg>
    <p class="person">Mark Lenner , <span class="person__title">President/CEO</span></p>
  </section>

  <section class="card card--back" aria-label="Business card back">
    <div class="ghost-name" aria-hidden="true">Trelvan</div>
    <ul class="services">
      <li>Web Design</li><li>Internet Marketing</li><br><li>Website Management</li>
    </ul>
    <div class="social">
      <span><i></i>@trelvanmedia</span>
      <span><i></i>trelvanmedia</span>
    </div>
  </section>
</body>
</html>
```